Quarrybend Marble & Tile Needs a Business Card

Attached you will find your logo, my photo and design guidelines for a new business card. The final design will need two separate files to create an embossed card. The cards will be printed by www.plinkprint.com (Instructions below)
Format is the Plink SQUARE card
Quarrybend Marble And Tile is a brick and mortar, retail stone and tile shop.
One the front:
Quarrybend Marble And Tile
Dorian Fesslock
Owner
24807 Hollis Verdant Blvd
Suite P & R
Charlotte, NC 28193
Cell: 704-583-7142
Web: www.QuarrybendMarbleAndTile.com
(Make each word of the domain a different or alternating color)
On the back;
Something that shows beautiful colorful tile
Follow the design guide closely please. For more information see this page that describes creating the spot gloss file: https://www.plinkprint.com/us/business-cards/design-guidelines-spot-gloss
The logo is what we would like to have raised spot glossed.
Format is the Plink SQUARE card. See attahced guidlines.

```html
<!DOCTYPE html>
<html lang="en">
<head>
<meta charset="utf-8">
<title>Quarrybend Marble &amp; Tile – Square Business Card</title>
<link rel="stylesheet" href="https://fonts.googleapis.com/css2?family=Cormorant+Garamond:wght@700&family=Montserrat:wght@400;500&display=swap">
<style>
  :root {
    --backdrop: #6b6b6b;
    --navy: #1f2b36;
    --navy-deep: #18222c;
    --rust: #a8401c;
    --gold: #c9862a;
    --sage: #8a8f78;
    --slate: #7d7f7a;
    --ink: #1f2b36;
    --paper: #ffffff;
    --cream: #f1ebe0;
  }
  html, body {
    margin: 0;
    width: 1200px;
    height: 800px;
    overflow: hidden;
    background: var(--backdrop);
  }
  .stage {
    position: relative;
    width: 1200px;
    height: 800px;
  }
  .card {
    position: absolute;
    top: 160px;
    width: 480px;
    height: 480px;
    box-sizing: border-box;
    border: 2px solid var(--gold);
    box-shadow: 0 18px 40px rgba(0,0,0,0.35);
    overflow: hidden;
  }

  /* Back of card */
  .card-back {
    left: 60px;
    background: var(--navy);
  }
  .tile-pattern {
    position: absolute;
    inset: 0;
    background:
      radial-gradient(circle at 50% 44%, rgba(168,64,28,0.55) 0%, rgba(168,64,28,0) 22%),
      radial-gradient(circle at 40% 52%, rgba(201,134,42,0.45) 0%, rgba(201,134,42,0) 26%),
      radial-gradient(circle at 60% 54%, rgba(138,143,120,0.45) 0%, rgba(138,143,120,0) 26%),
      radial-gradient(circle at 50% 50%, #2c3a47 0%, var(--navy-deep) 80%);
  }
  .back-brand {
    position: absolute;
    left: 0; right: 0;
    top: 300px;
    display: flex;
    align-items: center;
    justify-content: center;
    gap: 16px;
  }
  .brand-square {
    flex: none;
    width: 18px;
    height: 18px;
    background: var(--gold);
  }
  .back-brand .brand-name {
    font-family: "Montserrat", sans-serif;
    font-weight: 500;
    font-size: 22px;
    line-height: 1.5;
    letter-spacing: 0.2em;
    text-transform: uppercase;
    color: var(--cream);
  }

  /* Front of card */
  .card-front {
    left: 660px;
    background: var(--paper);
  }
  .portrait {
    position: absolute;
    left: 32px;
    top: 40px;
    width: 110px;
    height: 100px;
    box-sizing: border-box;
    border: 3px solid var(--gold);
    background: linear-gradient(160deg, #4a4f55, #23282e);
  }
  .front-brand {
    position: absolute;
    right: 32px;
    top: 58px;
    display: flex;
    align-items: center;
    gap: 12px;
  }
  .front-brand .brand-name {
    font-family: "Montserrat", sans-serif;
    font-weight: 500;
    font-size: 15px;
    line-height: 1.5;
    letter-spacing: 0.2em;
    text-transform: uppercase;
    color: var(--navy);
  }
  .holder-name {
    position: absolute;
    left: 32px;
    top: 184px;
    margin: 0;
    font-family: "Cormorant Garamond", serif;
    font-weight: 700;
    font-size: 34px;
    line-height: 1;
    color: var(--ink);
  }
  .holder-role {
    position: absolute;
    left: 32px;
    top: 224px;
    margin: 0;
    font-family: "Montserrat", sans-serif;
    font-size: 14px;
    color: var(--rust);
  }
  .divider {
    position: absolute;
    left: 32px;
    top: 254px;
  }
  .contact-list {
    position: absolute;
    left: 32px;
    top: 274px;
    margin: 0;
    padding: 0;
    list-style: none;
    font-family: "Montserrat", sans-serif;
    font-size: 14px;
    color: var(--ink);
    letter-spacing: 0.02em;
  }
  .contact-list li {
    display: flex;
    align-items: center;
    gap: 10px;
    height: 30px;
  }
  .contact-list .phone { letter-spacing: 0.12em; font-size: 16px; }
  .w-1 { color: var(--rust); }
  .w-2 { color: var(--gold); }
  .w-3 { color: var(--slate); }
  .address {
    position: absolute;
    right: 32px;
    top: 382px;
    margin: 0;
    text-align: right;
    font-family: "Montserrat", sans-serif;
    font-style: normal;
    font-size: 14px;
    line-height: 1.7;
    color: var(--ink);
  }
</style>
</head>
<body>
<main class="stage">

  <section class="card card-back" aria-label="Card back">
    <div class="tile-pattern" role="img" aria-label="Colourful tile mosaic over an embossed navy rosette pattern"></div>
    <div class="back-brand">
      <span class="brand-square"></span>
      <span class="brand-name">Quarrybend<br>Marble &amp; Tile</span>
    </div>
  </section>

  <section class="card card-front" aria-label="Card front">
    <div class="portrait" role="img" aria-label="Portrait photo of the owner"></div>

    <div class="front-brand">
      <span class="brand-square"></span>
      <span class="brand-name">Quarrybend<br>Marble &amp; Tile</span>
    </div>

    <h1 class="holder-name">Dorian Fesslock</h1>
    <p class="holder-role">Owner</p>

    <svg class="divider" width="412" height="4" viewBox="0 0 412 4" aria-hidden="true">
      <line x1="0" y1="2" x2="412" y2="2" stroke="var(--navy)" stroke-width="2" stroke-dasharray="14 6 4 6"/>
      <line x1="0" y1="2" x2="412" y2="2" stroke="var(--rust)" stroke-width="2" stroke-dasharray="0 60 22 38"/>
    </svg>

    <ul class="contact-list">
      <li>
        <svg width="15" height="15" viewBox="0 0 24 24" aria-hidden="true"><path fill="var(--rust)" d="M6.6 10.8a15.1 15.1 0 0 0 6.6 6.6l2.2-2.2a1 1 0 0 1 1-.25 11.4 11.4 0 0 0 3.6.57 1 1 0 0 1 1 1V20a1 1 0 0 1-1 1A17 17 0 0 1 3 4a1 1 0 0 1 1-1h3.5a1 1 0 0 1 1 1c0 1.25.2 2.45.57 3.57a1 1 0 0 1-.25 1z"/></svg>
        <span class="phone">704-583-7142</span>
      </li>
      <li>
        <svg width="15" height="15" viewBox="0 0 24 24" aria-hidden="true"><rect x="2" y="5" width="20" height="14" fill="var(--rust)"/><path d="M2 5l10 8 10-8" fill="none" stroke="#fff" stroke-width="1.6"/></svg>
        <span>info@<span class="w-1">Quarrybend</span><span class="w-2">Marble</span><span class="w-3">And</span><span class="w-3">Tile</span>.com</span>
      </li>
      <li>
        <svg width="15" height="15" viewBox="0 0 24 24" aria-hidden="true"><g fill="none" stroke="var(--rust)" stroke-width="2"><circle cx="12" cy="12" r="9"/><ellipse cx="12" cy="12" rx="4" ry="9"/><path d="M3 12h18M5 7h14M5 17h14"/></g></svg>
        <span>www.<span class="w-1">Quarrybend</span><span class="w-2">Marble</span><span class="w-3">And</span><span class="w-3">Tile</span>.com</span>
      </li>
    </ul>

    <address class="address">
      24807 Hollis Verdant Blvd<br>
      Suite P &amp; R<br>
      Charlotte, NC 28193
    </address>
  </section>

</main>
</body>
</html>
```